Packaging design Project - for lovers of the distant lands of the Andes and it's organic culture

Oyé Oyé, friends of the organic terroir! Lovers of the distant lands and the Andes, this mission is for you!
Our baby, Verdant Ridge, is preparing for birth! This is your chance to make us dream.
Our values: Giving life to the Authentic Terroir of Bolivia. For it ; provide sustainable solutions for the local terroir of our organic crops.

What is the terroir? (french word). It’s that connection to Human and Earth. Humanity is respect for culture, ancestral know-how, artisanal work. The Earth is the environment, the ecology, this is what the Indians called the Pachamama.

At an altitude of 4200m, La Quinoa de Verdant Ridge is not cultivated in the plains with combine harvesters. It is cultivated by hand on the feet and on the mountainside. The fallow (66% of the land) allows the soil and the Gods of the Andean cosmovision to come to life.
Our mission is to bring these values to life through these products that we import; White Quinoa , red, Duo (red and white) and Trio (red, black and white).
For this, we are looking for a packaging design. You bring creativity and together we validate the content !

The finished product is intended for end consumers (specialized organic store for example). Its format is 18cm high x 8.5cm long and 4.5cm wide. We therefore need a graphic charter for the entire packaging; or 4 sides totaling 26 cm for 18 cm high. You will mainly work on the visual of the main page (18x8.5), illustration of our committed values through the colors of Bolivia: Red, Yellow and Green. The country being very colorful by nature (google search: "Aguayo cloth") we want to create a breath of life through the liveliness of the colors, that the products are obvious, just like these famous Bolivian Aguayo.
Our Quinoa comes from an authentic terroir. It is harvested by hand and is very rich in nutrition.
We had already worked on packaging, which we want to improve and make more alive. It’s true that the black print kraft background isn’t the best.
Here are some snippets of text taken from this first packaging:
"While the Quinoa of the plains depletes the soils of the Bolivian altiplano ..."
"The Verdant Ridge Quinoa comes from areas that are difficult to access, at the foot and on the mountainside where the cultivation is done by hand and with respect for ancestral traditions"
Mountain Quinoa committed!
Provides a local solution for the Bolivian terroir.
By respecting the Earth: the Pachamama with the fallow of 66% of the land. A return to the sources, as in the time of the Incas, letting the llamas make the biodiversity of the high plains flourish.
By respect for the Human Being and for future generations. Cultivated and distributed preserving the essence of Andean culture, the rights and croyances of Quechua producers and honoring the values of the Bolivian people.

In summary, I invite you to discover the energy of the project through this video: https://www.clipvault-example.net/watch?v=Qz4LmRw8TkP
And these few images (attachments)…
And our logo of course on the PDF of our project presentation!

Note: Ideally, the design could include a visual of the raw Quinoa so client could see the product on the packaging. (as enclosed pictures!!!)

And most of all... have fun! Let your creativity EXPLODE! That's exactly what we want you to do. Just plenty be yourself... that's how our client will say 'Whaow!' looking at your art!

enjoy!

Target Market(s)

Premium Quinoa consumers. - Engaged consumers for causes and belief throught their product consumption

Font styles to use
Other font styles liked:
• earth quest (for head lines)

Colors
acd136
9bcb3c
ec1f27
f04a50
f78f20
f37122
ffc214
fece3e
fbed22

Requirements
Must have
• Colors (red, green and yellow)
Mountain as backgroud (enclosed)
Quinoa field on the feet or aside the mountain
Autoctones (people)
Quinoa grains (as it is raw)
Nice to have
• Detail of expressing Quinoa is handly cultivated (hand harvest)
Tipical houses in the back
Aguayo motifs (for the graphic charter maybe?)

```html
<!DOCTYPE html>
<html lang="fr">
<head>
<meta charset="utf-8">
<title>Quinoa de Montagnes de Bolivie – Verdant Ridge</title>
<link rel="stylesheet" href="https://fonts.googleapis.com/css2?family=Kaushan+Script&family=Montserrat:wght@300;400;700&display=swap">
<style>
  :root {
    --red: #d8262a;
    --orange: #e8692a;
    --amber: #f09a1f;
    --yellow: #f3bd1b;
    --olive: #a3a33a;
    --green: #13894a;
    --white: #ffffff;
    --backdrop: #f2ede4;
    --grain-light: #e6d6b8;
    --grain-mid: #c9ad82;
    --scoop: #7b4a2c;
  }
  * { box-sizing: border-box; margin: 0; padding: 0; }
  html, body {
    width: 1200px;
    height: 1133px;
    overflow: hidden;
    background: var(--backdrop);
  }
  .canvas {
    position: relative;
    width: 1200px;
    height: 1133px;
  }
  .front-panel {
    position: absolute;
    left: 341px;
    top: 20px;
    width: 518px;
    height: 1093px;
    overflow: hidden;
    color: var(--white);
    background: linear-gradient(180deg,
      var(--red) 0%,
      var(--orange) 24%,
      var(--amber) 38%,
      var(--yellow) 49%,
      var(--olive) 70%,
      var(--green) 100%);
    font-family: "Montserrat", sans-serif;
  }
  .product-title {
    position: absolute;
    left: 22px;
    top: 40px;
    width: 474px;
    text-align: center;
    font-family: "Kaushan Script", cursive;
    font-size: 168px;
    line-height: 1.2;
    font-weight: 400;
  }
  .product-origin {
    position: absolute;
    left: 0;
    top: 262px;
    width: 518px;
    text-align: center;
    font-weight: 700;
    font-size: 26px;
    letter-spacing: 0.3px;
  }
  .emblem-art {
    position: absolute;
    left: 36px;
    top: 318px;
    width: 289px;
    height: 239px;
    border-radius: 48% 52% 30% 30% / 60% 60% 20% 20%;
    background: linear-gradient(160deg, rgba(255,255,255,0.95), rgba(255,255,255,0.8));
  }
  .brand-name {
    position: absolute;
    left: 34px;
    top: 566px;
    font-weight: 700;
    font-size: 46px;
    line-height: 1;
  }
  .brand-tagline {
    position: absolute;
    left: 54px;
    top: 622px;
    font-family: "Kaushan Script", cursive;
    font-size: 34px;
    line-height: 1;
  }
  .nutrition-claim {
    position: absolute;
    left: 36px;
    top: 688px;
    font-weight: 300;
    font-size: 24px;
    letter-spacing: 0.3px;
  }
  .feature-list {
    position: absolute;
    left: 34px;
    top: 750px;
    display: flex;
    gap: 30px;
    list-style: none;
  }
  .feature {
    display: flex;
    align-items: center;
    gap: 14px;
    font-weight: 400;
    font-size: 19px;
    line-height: 1.3;
  }
  .feature-icon {
    width: 48px;
    height: 48px;
    flex: none;
  }
  .grain-photo {
    position: absolute;
    left: 0;
    top: 875px;
    width: 335px;
    height: 218px;
    border-radius: 0 70% 0 0 / 0 85% 0 0;
    background:
      radial-gradient(ellipse at 18% 20%, var(--scoop) 0 14%, transparent 15%),
      radial-gradient(ellipse at 45% 70%, var(--grain-light), var(--grain-mid));
  }
</style>
</head>
<body>
<main class="canvas">
  <section class="front-panel">
    <h1 class="product-title">Quinoa</h1>
    <p class="product-origin">DE MONTAGNES DE BOLIVIE</p>

    <div class="emblem-art" role="img" aria-label="Illustration of an Andean figure in a knitted hat before starry mountain peaks"></div>

    <p class="brand-name">Verdant Ridge</p>
    <p class="brand-tagline">Terroir Authentique</p>

    <p class="nutrition-claim">A HAUTE VALEUR NUTRITIVE</p>

    <ul class="feature-list">
      <li class="feature">
        <svg class="feature-icon" viewBox="0 0 48 48" fill="none" stroke="#fff" stroke-width="2" stroke-linecap="round" stroke-linejoin="round" aria-hidden="true">
          <circle cx="24" cy="24" r="22"/>
          <path d="M24 28 V15"/>
          <path d="M24 20 C20 19 18 16 18 13 C21 13 24 16 24 20"/>
          <path d="M24 18 C28 17 30 14 30 11 C27 11 24 14 24 18"/>
          <path d="M12 30 L18 30 C21 30 23 32 26 32 L33 30 C35 29.5 36 31 34.5 32 L27 36 L14 36"/>
        </svg>
        <span>Harvest<br>by Hand</span>
      </li>
      <li class="feature">
        <svg class="feature-icon" viewBox="0 0 48 48" fill="none" stroke="#fff" stroke-width="2" stroke-linecap="round" stroke-linejoin="round" aria-hidden="true">
          <circle cx="24" cy="24" r="22"/>
          <path d="M10 32 L19 18 L24 25 L28 20 L38 32 Z"/>
          <path d="M19 18 L17 24 M28 20 L29 26"/>
        </svg>
        <span>From The<br>Mountains</span>
      </li>
    </ul>

    <div class="grain-photo" role="img" aria-label="Photograph of raw quinoa grains with a wooden scoop"></div>
  </section>
</main>
</body>
</html>
```